Building signage and email signature

Our business specialises in alloy wheel refurbishment. We have just moved to a new premises and would like the front of the building to stand out to passing traffic.
We would like for someone to create a design for us to print onto vinyl and cover the front of the building. I have enclosed pictures of the unit and would like the following areas covered in images:
- area to the right hand side of the entrance to be covered complete 2570mm (W) x 2820mm (H)
- 8 x panels that are currently painted blue under the windows 1050mm (W) 730mm (H)
You can use our website for some inspiration www.the-rimforge.com. We have instagram, facebook and twitter accounts and would like these promoted on the front of the building aswell.
I have uploaded files with our logos, if you are going to use them please can you change the orange in the logo to a sunflower yellow. You are welcome to use the images in our gallery on the website, on facebook or instagram to aid your design. I can provide better quality images at a later date.
We'd also like an email signature created with a similar theme to the front of the building.
We may ask the successful designer to undertake the re-design of our website, so if you have skills in both areas that would be beneficial and can be discussed at a later date.
Messages to communicate through the design:
- company name
- website address
- specialist alloy wheel refurbishment
- wheel straightening
- alloy wheel welding
- twitter
- facebook
- instagram
- telephone number
- images of work carried out
Ideas for the visual style: bold, modern
regards
Colin

```html
<!DOCTYPE html>
<html lang="en">
<head>
<meta charset="utf-8">
<title>The Rimforge – Building Signage</title>
<link rel="stylesheet" href="https://fonts.googleapis.com/css2?family=Source+Sans+3:wght@600;700&display=swap">
<style>
  :root {
    --bg: #121c1f;
    --swoosh: #5c5347;
    --panel-line: #3a3b26;
    --sunflower: #f8d23d;
    --white: #ffffff;
    --tile: #d9d9d9;
    --shadow: rgba(0, 0, 0, 0.75);
  }
  * { margin: 0; padding: 0; box-sizing: border-box; }
  html, body { width: 1088px; height: 1200px; overflow: hidden; background: var(--bg); }
  .signage {
    position: relative; width: 1088px; height: 1200px; overflow: hidden;
    background: var(--bg);
    font-family: "Source Sans 3", "Myriad Pro", sans-serif;
    color: var(--sunflower);
  }
  .swoosh { position: absolute; inset: 0; }
  .panel { position: absolute; border: 1px solid var(--panel-line); }
  .col-left { left: 31px; width: 502px; }
  .col-right { left: 554px; width: 502px; }
  .row-1 { top: 32px; height: 178px; }
  .row-2 { top: 236px; height: 182px; }
  .row-3 { top: 440px; height: 182px; }
  .row-4 { top: 644px; height: 182px; }
  .row-5 { top: 850px; height: 180px; }
  .row-6 { top: 1052px; height: 116px; }

  .brand { position: absolute; left: 262px; top: 52px; height: 120px; display: flex; align-items: center; gap: 18px; }
  .brand-dot { width: 26px; height: 26px; border-radius: 50%; background: var(--sunflower); flex: none; }
  .brand-name {
    font-weight: 600; font-size: 112px; line-height: 1;
    color: var(--sunflower); white-space: nowrap;
  }

  .social-networks {
    position: absolute; left: 50px; top: 240px; width: 468px;
    display: flex; justify-content: space-between;
  }
  .social-tile { width: 78px; height: 78px; border-radius: 10px; background: var(--tile); }
  .social-handle {
    position: absolute; left: 48px; top: 322px;
    font-weight: 700; font-size: 84px; line-height: 1;
    text-shadow: 3px 3px 0 var(--shadow); white-space: nowrap;
  }

  .contact-line {
    position: absolute; left: 564px; display: flex; align-items: center; gap: 12px;
    color: var(--white); font-weight: 700; text-shadow: 2px 2px 0 var(--shadow); white-space: nowrap;
  }
  .contact-web { top: 246px; font-size: 35px; line-height: 46px; letter-spacing: 0.5px; }
  .contact-phone { top: 304px; font-size: 66px; line-height: 1; letter-spacing: 2px; }
  .contact-mail { top: 375px; font-size: 35px; line-height: 46px; letter-spacing: 0.5px; }
  .contact-line svg { flex: none; }

  .service {
    position: absolute; font-weight: 700; font-size: 62px; line-height: 66px;
    text-shadow: 3px 3px 0 var(--shadow); white-space: nowrap;
  }
  .service-dot { position: absolute; width: 34px; height: 34px; border-radius: 50%; background: var(--sunflower); }
  .svc-refurb { left: 100px; top: 434px; }
  .svc-weld { left: 625px; top: 434px; }
  .svc-straight { left: 102px; top: 634px; }
  .dot-refurb { left: 46px; top: 488px; }
  .dot-weld { left: 570px; top: 488px; }
  .dot-straight { left: 46px; top: 692px; }

  .extras {
    position: absolute; left: 556px; top: 638px;
    font-weight: 600; font-size: 50px; line-height: 52px;
    text-shadow: 3px 3px 0 var(--shadow); white-space: nowrap;
  }
  .extras-title { font-size: 44px; margin-bottom: 12px; }

  .work-photo {
    position: absolute; top: 850px; width: 500px; height: 180px;
    border: 2px solid var(--white); border-radius: 14px;
  }
  .photo-wheels { left: 32px; background: linear-gradient(135deg, #8a8f94 0%, #c9ccce 40%, #6e7175 70%, #a9acae 100%); }
  .photo-car { left: 556px; background: linear-gradient(90deg, #e7902a 0%, #e7902a 20%, #1d1f22 28%, #2a2c2f 70%, #f0a33a 82%, #f4a93d 100%); }
</style>
</head>
<body>
<main class="signage">
  <svg class="swoosh" width="1088" height="1200" viewBox="0 0 1088 1200" aria-hidden="true">
    <path d="M0,184 C520,170 1010,520 1058,1200 L990,1200 C940,820 620,590 0,580 Z" fill="var(--swoosh)"/>
  </svg>

  <div class="panel col-left row-1"></div>
  <div class="panel col-right row-1"></div>
  <div class="panel col-left row-2"></div>
  <div class="panel col-right row-2"></div>
  <div class="panel col-left row-3"></div>
  <div class="panel col-right row-3"></div>
  <div class="panel col-left row-4"></div>
  <div class="panel col-right row-4"></div>
  <div class="panel col-left row-5"></div>
  <div class="panel col-right row-5"></div>
  <div class="panel col-left row-6"></div>
  <div class="panel col-right row-6"></div>

  <header class="brand">
    <span class="brand-dot"></span>
    <span class="brand-name">the rimforge</span>
  </header>

  <div class="social-networks" aria-hidden="true">
    <span class="social-tile"></span><span class="social-tile"></span><span class="social-tile"></span>
  </div>
  <p class="social-handle">therimforge</p>

  <p class="contact-line contact-web">
    <svg width="46" height="46" viewBox="0 0 46 46" aria-hidden="true">
      <g fill="none" stroke="var(--sunflower)" stroke-width="2.5">
        <circle cx="23" cy="23" r="20"/>
        <ellipse cx="23" cy="23" rx="9" ry="20"/>
        <line x1="3" y1="23" x2="43" y2="23"/>
        <path d="M6,13 H40 M6,33 H40"/>
      </g>
    </svg>
    www.the-rimforge.com
  </p>
  <p class="contact-line contact-phone">
    <svg width="46" height="46" viewBox="0 0 46 46" aria-hidden="true">
      <path d="M10,4 L18,12 L13,18 C16,25 21,30 28,33 L34,28 L42,36 L36,42 C20,40 6,26 4,10 Z" fill="var(--sunflower)"/>
    </svg>
    01632 960482
  </p>
  <p class="contact-line contact-mail">
    <svg width="46" height="40" viewBox="0 0 46 40" aria-hidden="true">
      <g fill="none" stroke="var(--sunflower)" stroke-width="2.5">
        <rect x="3" y="8" width="36" height="26"/>
        <path d="M3,8 L21,22 L39,8"/>
      </g>
    </svg>
    info@the-rimforge.com
  </p>

  <span class="service-dot dot-refurb"></span>
  <h2 class="service svc-refurb">Alloy Wheel<br>Refurbishment</h2>
  <span class="service-dot dot-weld"></span>
  <h2 class="service svc-weld">Alloy Wheel<br>Welding</h2>
  <span class="service-dot dot-straight"></span>
  <h2 class="service svc-straight">Alloy Wheel<br>Straightening</h2>

  <div class="extras">
    <p class="extras-title">Also:</p>
    <p>Window Tinting</p>
    <p>Brake Caliper Painting</p>
  </div>

  <div class="work-photo photo-wheels" role="img" aria-label="Photo of refurbished silver alloy wheels laid out on a workshop floor"></div>
  <div class="work-photo photo-car" role="img" aria-label="Photo of an orange sports car with a black alloy wheel and red brake caliper"></div>
</main>
</body>
</html>
```